Valmora Company needs a Business Card Design

We just opened our business recently and we need a business card design. Our basic product are clothes and accessories. We would like to see designs that use bright colors like pink, light blue and purple. In addition to that kindly include also our address in the business card which our main office is located in Los Angeles, California.
The final design should communicate that we have affordable price yet high quality brand.

Target Market(s)

young and middle age women

Industry/Entity Type

Business

Contact Information for Business Card

Valmora Apparel and Accessories 4873 North Bellcrest St. Los Angeles California
Tel: 555-318-6492

Logo Text

Valmora's Apparel and Accessories

Font styles to use
Serif

Requirements
Must have
• there should be a graphic of a sexy lady wearing an elegant dress at the upper left corner of the business card.

```html
<!DOCTYPE html>
<html lang="en">
<head>
<meta charset="utf-8">
<title>Valmora Apparel and Accessories – Business Card</title>
<link rel="stylesheet" href="https://fonts.googleapis.com/css2?family=Alegreya:ital,wght@0,400;0,700;1,400&display=swap">
<style>
  :root {
    --page-bg: #e8e5e1;
    --card-edge: #b236ae;
    --card-face-light: #ffffff;
    --card-face-shade: #ececec;
    --brand-pink: #d43ab8;
    --ink: #1c1c1c;
    --ink-soft: #555555;
    --figure-dark: #1a1a1a;
    --figure-mist: #d9d9d9;
  }
  html, body {
    margin: 0;
    width: 1200px;
    height: 818px;
    overflow: hidden;
    background: var(--page-bg);
  }
  .canvas {
    position: relative;
    width: 1200px;
    height: 818px;
    display: flex;
    align-items: center;
    justify-content: center;
  }
  .business-card {
    position: relative;
    width: 1040px;
    height: 600px;
    box-sizing: border-box;
    border: 20px solid var(--card-edge);
    border-radius: 4px;
    background: linear-gradient(135deg, var(--card-face-shade) 0%, var(--card-face-light) 45%, var(--card-face-light) 100%);
    box-shadow: 0 12px 30px rgba(0,0,0,0.18);
    font-family: "Alegreya", Georgia, serif;
    color: var(--ink);
  }
  .figure-art {
    position: absolute;
    left: 60px;
    bottom: 40px;
    width: 440px;
    height: 330px;
    border-radius: 2px;
    background: linear-gradient(90deg, var(--figure-dark) 0%, #4a4a4a 35%, var(--figure-mist) 70%, rgba(255,255,255,0) 100%);
    opacity: 0.85;
  }
  .text-block {
    position: absolute;
    right: 56px;
    top: 36px;
    text-align: right;
  }
  .brand-name {
    margin: 0;
    font-weight: 700;
    font-size: 54px;
    line-height: 1;
    color: var(--brand-pink);
  }
  .brand-tagline {
    margin: 14px 0 0;
    font-style: italic;
    font-size: 46px;
    line-height: 1.1;
  }
  .person {
    margin-top: 44px;
  }
  .person-name {
    margin: 0;
    font-style: italic;
    font-size: 54px;
    line-height: 1;
  }
  .person-role {
    margin: 2px 0 0;
    font-size: 22px;
    color: var(--ink-soft);
  }
  .contact {
    position: absolute;
    right: 56px;
    bottom: 52px;
    text-align: right;
    font-size: 30px;
    line-height: 1.25;
  }
  .contact-line {
    display: flex;
    justify-content: flex-end;
    align-items: center;
    gap: 14px;
  }
  .contact-line.phone { margin-bottom: 26px; }
  .contact-icon { width: 20px; height: 24px; fill: var(--ink); }
  .contact-icon.spacer { visibility: hidden; }
</style>
</head>
<body>
<main class="canvas">
  <article class="business-card">
    <div class="figure-art" role="img" aria-label="Illustration of an elegant lady silhouette in a long evening gown with pink gloves, with faded echo silhouettes behind"></div>

    <header class="text-block">
      <h1 class="brand-name">Valmora</h1>
      <p class="brand-tagline">Apparel and Accessories</p>
      <div class="person">
        <p class="person-name">Your Name</p>
        <p class="person-role">Position</p>
      </div>
    </header>

    <address class="contact" style="font-style: normal;">
      <div class="contact-line phone">
        <span>555-318-6492</span>
        <svg class="contact-icon" viewBox="0 0 20 24" aria-hidden="true">
          <path d="M5 1 L9 1 L10 7 L7 9 Q9 15 13 17 L15 14 L20 16 L19 21 Q18 23 15 23 Q3 19 1 5 Q1 2 5 1 Z"/>
        </svg>
      </div>
      <div class="contact-line">
        <span>4873 North Bellcrest St</span>
        <svg class="contact-icon" viewBox="0 0 20 24" aria-hidden="true">
          <path d="M10 0 Q19 0 19 9 Q19 15 10 24 Q1 15 1 9 Q1 0 10 0 Z M10 5 A4 4 0 1 0 10.01 5 Z" fill-rule="evenodd"/>
        </svg>
      </div>
      <div class="contact-line">
        <span>Los Angeles California</span>
        <svg class="contact-icon spacer" viewBox="0 0 20 24" aria-hidden="true"></svg>
      </div>
    </address>
  </article>
</main>
</body>
</html>
```